VOMRA Pty Ltd Business Card

Looking for a simple yet eye-catching double-sided business card design using my company logo on one side and contact details on the other.

Target Market(s)

Government

Industry/Entity Type

Communication Systems Engineering

Contact Information for Business Card

VOMRA Pty Ltd

Requirements
Nice to have
• Would be great to have a QR code so details can be scanned into contacts

```html
<!DOCTYPE html>
<html lang="en">
<head>
<meta charset="utf-8">
<title>VOMRA Pty Ltd Business Card</title>
<link rel="stylesheet" href="https://fonts.googleapis.com/css2?family=Open+Sans:wght@400;700&display=swap">
<style>
  :root {
    --slate: #353e45;
    --ink: #2f373e;
    --paper: #ffffff;
    --stage: #d8dadc;
    --rule: #3a4249;
  }
  * { box-sizing: border-box; margin: 0; padding: 0; }
  html, body {
    width: 1200px; height: 780px; overflow: hidden;
    background: var(--stage);
    font-family: "Open Sans", sans-serif;
  }
  .stage {
    width: 1200px; height: 780px;
    display: flex; align-items: center; justify-content: center; gap: 44px;
  }
  .card {
    position: relative;
    width: 525px; height: 300px;
    border-radius: 18px;
    overflow: hidden;
    box-shadow: 0 10px 28px rgba(0,0,0,.18);
  }
  /* Front: logo side */
  .card--front {
    background: var(--slate);
    display: flex; align-items: center; justify-content: center; gap: 18px;
  }
  .wordmark {
    font-weight: 700; letter-spacing: 2px; line-height: 1;
  }
  .card--front .wordmark { color: var(--paper); font-size: 78px; }
  .mark-dot {
    width: 22px; height: 22px; border-radius: 50%;
    background: var(--paper);
  }
  /* Back: contact side */
  .card--back { background: var(--paper); color: var(--ink); }
  .brand {
    position: absolute; left: 34px; top: 92px;
    display: flex; align-items: center; gap: 10px;
  }
  .brand .mark-dot { width: 14px; height: 14px; background: var(--ink); }
  .brand .wordmark { font-size: 46px; color: var(--ink); }
  .divider {
    position: absolute; left: 252px; top: 70px;
    width: 1.5px; height: 130px; background: var(--rule);
  }
  .person { position: absolute; left: 280px; top: 84px; }
  .person__name { font-size: 27px; font-weight: 700; line-height: 1.1; color: var(--slate); }
  .person__role { font-size: 15px; margin-top: 2px; }
  .contact { list-style: none; margin-top: 12px; }
  .contact li {
    display: flex; align-items: center; gap: 9px;
    font-size: 16.5px; line-height: 23px;
  }
  .contact svg { width: 14px; height: 14px; flex: none; fill: var(--slate); }
  .address {
    position: absolute; left: 30px; bottom: 38px;
    font-size: 15px;
  }
  .band { position: absolute; left: 0; bottom: 0; width: 100%; height: 28px; }
</style>
</head>
<body>
<main class="stage">
  <section class="card card--front" aria-label="Card front">
    <span class="mark-dot"></span>
    <span class="wordmark">VOMRA</span>
  </section>

  <section class="card card--back" aria-label="Card back">
    <div class="brand">
      <span class="mark-dot"></span>
      <span class="wordmark">VOMRA</span>
    </div>
    <div class="divider"></div>
    <div class="person">
      <h1 class="person__name">Jordan Hale</h1>
      <p class="person__role">Co-Founder</p>
      <ul class="contact">
        <li>
          <svg viewBox="0 0 24 24" aria-hidden="true"><path d="M6.6 10.8a15.5 15.5 0 0 0 6.6 6.6l2.2-2.2c.3-.3.7-.4 1-.2 1.1.4 2.3.6 3.6.6.6 0 1 .4 1 1V20c0 .6-.4 1-1 1A17 17 0 0 1 3 4c0-.6.4-1 1-1h3.5c.6 0 1 .4 1 1 0 1.3.2 2.5.6 3.6.1.3 0 .7-.2 1z"/></svg>
          (555) 014-2290
        </li>
        <li>
          <svg viewBox="0 0 24 24" aria-hidden="true"><path d="M12 2a10 10 0 1 0 0 20 10 10 0 0 0 0-20zm6.9 6h-3a15 15 0 0 0-1.3-3.9A8 8 0 0 1 18.9 8zM12 4c.9 1.2 1.6 2.6 2 4h-4c.4-1.4 1.1-2.8 2-4zM4.3 14a8 8 0 0 1 0-4h3.4a16 16 0 0 0 0 4zm.8 2h3a15 15 0 0 0 1.3 3.9A8 8 0 0 1 5.1 16zm3-8h-3a8 8 0 0 1 4.3-3.9C8.8 5.3 8.4 6.6 8.1 8zM12 20c-.9-1.2-1.6-2.6-2-4h4c-.4 1.4-1.1 2.8-2 4zm2.3-6H9.7a14 14 0 0 1 0-4h4.6a14 14 0 0 1 0 4zm.3 5.9c.6-1.2 1-2.5 1.3-3.9h3a8 8 0 0 1-4.3 3.9zm1.7-5.9a16 16 0 0 0 0-4h3.4a8 8 0 0 1 0 4z"/></svg>
          www.vomra.com.au
        </li>
        <li>
          <svg viewBox="0 0 24 24" aria-hidden="true"><path d="M3 5h18c.6 0 1 .4 1 1v12c0 .6-.4 1-1 1H3c-.6 0-1-.4-1-1V6c0-.6.4-1 1-1zm1 2.4V17h16V7.4l-8 5.3z M5.2 7 12 11.5 18.8 7z"/></svg>
          admin@vomra.com.au
        </li>
      </ul>
    </div>
    <p class="address">27-29 Marlow Street Kelbrook NSW 2031 Australia</p>
    <svg class="band" viewBox="0 0 525 28" preserveAspectRatio="none" aria-hidden="true">
      <rect width="525" height="28" fill="#353e45"/>
      <polygon points="118,0 134,0 150,28 134,28" fill="#ffffff"/>
    </svg>
  </section>
</main>
</body>
</html>
```